iOS7 test prep app

I need 3 basic screens and 2 product images for an iOS7 app I am prototyping. I provided lots of detail in the attached brief. This is an education product, so warm colors (especially reds) work best.

If you've done flat design for mobile products, please take a look ... Thanks!

Greetings, all. Thank you for your submissions. I am meeting with my product development team this week to review your submissions, and will select a designer before the end of the week. I appreciate your patience with my process, and thank you again for your interest in my project. I'll be back to you soon ... -Gerald

```html
<!DOCTYPE html>
<html lang="en">
<head>
<meta charset="utf-8">
<title>Test Prep – Question Screens</title>
<link rel="stylesheet" href="https://fonts.googleapis.com/css2?family=Cabin:wght@400;600;700&family=Open+Sans:wght@600;700&display=swap">
<style>
  :root {
    --page-bg: #f3f3f1;
    --header-top: #2089c2;
    --header-bottom: #13659d;
    --sky: #86cdf1;
    --sky-light: #b6e1f6;
    --cloud: #d7effb;
    --ground-pink: #f3c6dc;
    --card-bg: #ffffff;
    --card-border: #c9d9e4;
    --text-dark: #3d3d3d;
    --option-top: #ffffff;
    --option-bottom: #d4d4d4;
    --option-text: #333333;
    --orange-top: #ff7a1e;
    --orange-bottom: #ec4a05;
    --blue-top: #2b8fd0;
    --blue-bottom: #1663a6;
    --green-top: #a9d84a;
    --green-bottom: #7dba22;
    --red: #d6262b;
    --help-blue: #1f8cc8;
  }
  * { box-sizing: border-box; margin: 0; padding: 0; }
  html, body { width: 1123px; height: 1200px; overflow: hidden; background: var(--page-bg); }
  .stage {
    position: absolute; left: 21px; top: 95px;
    width: 800px; height: 748px;
    transform: scale(1.35); transform-origin: 0 0;
  }
  .screen {
    position: absolute; top: 0; width: 370px; height: 748px;
    background: linear-gradient(var(--sky) 0%, var(--sky) 55%, var(--sky-light) 100%);
    overflow: hidden; font-family: "Cabin", sans-serif;
  }
  .screen--question { left: 0; }
  .screen--answer { left: 430px; }
  .app-header {
    position: absolute; left: 0; top: 0; width: 100%; height: 52px;
    background: linear-gradient(var(--header-top), var(--header-bottom));
    color: #fff;
  }
  .menu-icon { position: absolute; left: 20px; top: 17px; width: 30px; height: 17px; }
  .menu-icon span { display: block; height: 3px; background: #fff; margin-bottom: 4px; }
  .app-header h1 {
    position: absolute; left: 110px; top: 17px;
    font: 700 15px/18px "Open Sans", sans-serif; letter-spacing: 0.2px;
  }
  .scenery { position: absolute; left: 0; bottom: 0; width: 100%; height: 240px;
    background: radial-gradient(ellipse 60% 40% at 60% 65%, var(--cloud), transparent 70%),
                radial-gradient(ellipse 40% 35% at 15% 70%, var(--cloud), transparent 70%); }
  .ground { position: absolute; left: -20px; bottom: -30px; width: 410px; height: 60px;
    border-radius: 50% 50% 0 0; background: var(--ground-pink); border-top: 6px solid #fff; }
  .question-card {
    position: absolute; left: 22px; top: 76px; width: 328px; height: 186px;
    background: var(--card-bg); border: 1px solid var(--card-border); border-radius: 4px;
  }
  .help-icon { position: absolute; left: 10px; top: 78px; }
  .question-card p {
    position: absolute; left: 57px; top: 16px; width: 262px;
    font-size: 15px; line-height: 26px; color: var(--text-dark);
  }
  .option {
    position: absolute; left: 22px; width: 328px; height: 42px;
    border-radius: 4px; border: 1px solid #c2c2c2;
    background: linear-gradient(var(--option-top) 0%, #f1f1f1 50%, var(--option-bottom) 52%, #e3e3e3 100%);
    font: 700 14.5px/40px "Open Sans", sans-serif; color: var(--option-text);
    padding-left: 16px; text-transform: uppercase;
  }
  .option svg { position: absolute; right: 16px; top: 11px; }
  .option--a { top: 279px; } .option--b { top: 337px; }
  .option--c { top: 397px; } .option--d { top: 457px; }
  .option--correct { background: linear-gradient(var(--green-top), var(--green-bottom)); border-color: #6ea51f; }
  .btn {
    position: absolute; height: 46px; border-radius: 3px; color: #fff; text-align: center;
    font: 600 16px/46px "Open Sans", sans-serif; text-transform: uppercase;
  }
  .btn--orange { background: linear-gradient(var(--orange-top), var(--orange-bottom)); border: 1px solid #d34400; }
  .btn--blue { background: linear-gradient(var(--blue-top), var(--blue-bottom)); border: 1px solid #125a95; }
  .btn--confidence { left: 106px; top: 526px; width: 156px; }
  .btn--submit { left: 105px; top: 676px; width: 158px; }
  .btn--save { left: 22px; top: 677px; width: 155px; }
  .btn--next { left: 194px; top: 676px; width: 156px; }
  .confidence-slider { position: absolute; left: 20px; top: 607px; }
  .explanation {
    position: absolute; left: 22px; top: 515px; width: 328px; height: 141px;
    background: var(--card-bg); border: 1px solid var(--card-border); border-radius: 4px;
    padding: 15px 17px; font-size: 14.5px; line-height: 23px; color: var(--text-dark);
  }
  .explanation strong { font-weight: 700; color: #222; }
</style>
</head>
<body>
<div class="stage">

  <section class="screen screen--question">
    <div class="scenery" role="img" aria-label="Soft clouds in a pale blue sky"></div>
    <div class="ground"></div>
    <header class="app-header">
      <div class="menu-icon"><span></span><span></span><span></span></div>
      <h1>QUESTION 7 OF 100</h1>
    </header>
    <div class="question-card">
      <svg class="help-icon" width="32" height="32" viewBox="0 0 32 32"><circle cx="16" cy="16" r="15" fill="var(--help-blue)" stroke="#0f5f8f"/><text x="16" y="23" text-anchor="middle" font-family="Open Sans, sans-serif" font-weight="700" font-size="20" fill="#fff">?</text></svg>
      <p>A patient presents to the emergency room with the following symptoms: Anxiety, dyspnea, rhonchi, fever, Oxygen saturation of 88%, and a pH of 7.21. The nurse realized that the patient suffering from:</p>
    </div>
    <div class="option option--a">A. Respiratory Alkalosis</div>
    <div class="option option--b">B. Metabolic Alkalosis</div>
    <div class="option option--c">C. Respiratory Acidosis</div>
    <div class="option option--d">D. Metabolic Acidosis</div>
    <div class="btn btn--orange btn--confidence">Confidence</div>
    <svg class="confidence-slider" width="330" height="40" viewBox="0 0 330 40">
      <circle cx="19" cy="20" r="18" fill="#fff" opacity=".6"/>
      <circle cx="19" cy="20" r="14" fill="var(--red)"/>
      <rect x="12" y="18.5" width="14" height="3" fill="#fff"/>
      <rect x="57" y="15" width="218" height="9" rx="4.5" fill="#d3d3d3"/>
      <rect x="57" y="15" width="140" height="9" rx="4.5" fill="var(--orange-bottom)"/>
      <circle cx="196" cy="19.5" r="11" fill="#f4f4f4" stroke="#bbb"/>
      <circle cx="196" cy="19.5" r="4" fill="#ddd"/>
      <circle cx="310" cy="20" r="18" fill="#fff" opacity=".6"/>
      <circle cx="310" cy="20" r="14" fill="#2f95d6"/>
      <rect x="303" y="18.5" width="14" height="3" fill="#fff"/>
      <rect x="308.5" y="13" width="3" height="14" fill="#fff"/>
    </svg>
    <div class="btn btn--blue btn--submit">Submit</div>
  </section>

  <section class="screen screen--answer">
    <div class="scenery" role="img" aria-label="Soft clouds in a pale blue sky"></div>
    <div class="ground"></div>
    <header class="app-header">
      <div class="menu-icon"><span></span><span></span><span></span></div>
      <h1>QUESTION 7 OF 100</h1>
    </header>
    <div class="question-card">
      <svg class="help-icon" width="32" height="32" viewBox="0 0 32 32"><circle cx="16" cy="16" r="15" fill="var(--help-blue)" stroke="#0f5f8f"/><text x="16" y="23" text-anchor="middle" font-family="Open Sans, sans-serif" font-weight="700" font-size="20" fill="#fff">?</text></svg>
      <p>A patient presents to the emergency room with the following symptoms: Anxiety, dyspnea, rhonchi, fever, Oxygen saturation of 88%, and a pH of 7.21. The nurse realized that the patient suffering from:</p>
    </div>
    <div class="option option--a">A. Respiratory Alkalosis
      <svg width="20" height="20" viewBox="0 0 20 20"><circle cx="10" cy="10" r="8.5" fill="#fff" stroke="var(--red)" stroke-width="2"/><path d="M7 7l6 6M13 7l-6 6" stroke="var(--red)" stroke-width="2.2"/></svg></div>
    <div class="option option--b">B. Metabolic Alkalosis
      <svg width="20" height="20" viewBox="0 0 20 20"><circle cx="10" cy="10" r="8.5" fill="#fff" stroke="var(--red)" stroke-width="2"/><path d="M7 7l6 6M13 7l-6 6" stroke="var(--red)" stroke-width="2.2"/></svg></div>
    <div class="option option--c option--correct">C. Respiratory Acidosis
      <svg width="20" height="20" viewBox="0 0 20 20"><circle cx="10" cy="10" r="8.5" fill="none" stroke="#4e7d12" stroke-width="1.5"/><path d="M6 10l3 3 5-6" fill="none" stroke="#4e7d12" stroke-width="1.8"/></svg></div>
    <div class="option option--d">D. Metabolic Acidosis
      <svg width="20" height="20" viewBox="0 0 20 20"><circle cx="10" cy="10" r="8.5" fill="#fff" stroke="var(--red)" stroke-width="2"/><path d="M7 7l6 6M13 7l-6 6" stroke="var(--red)" stroke-width="2.2"/></svg></div>
    <div class="explanation"><strong>The correct answer is C.</strong> A key symptom of respiratory distress syndrome is the inability of the respiratory system to exchange gases, resulting in respiratory. acidosis.</div>
    <div class="btn btn--orange btn--save">Save &amp; Close</div>
    <div class="btn btn--blue btn--next">Next Question</div>
  </section>

</div>
</body>
</html>
```